Business card for event manager / organizer "waiter service"

Draft of a new valuable business card for my company.
Events, personnel service providers, festivals

```html
<!DOCTYPE html>
<html lang="de">
<head>
<meta charset="utf-8">
<title>Nova Eventservice – Visitenkarte</title>
<link rel="stylesheet" href="https://fonts.googleapis.com/css2?family=Montserrat:ital,wght@0,700;0,800;1,900&family=Quicksand:wght@400&display=swap">
<style>
  :root {
    --bg-top: #2a2a2b;
    --bg-bottom: #161616;
    --frame: #0d0d0d;
    --orange: #ec6408;
    --gold: #e49b2c;
    --white: #ffffff;
    --muted: #c9c9c9;
    --photo-a: #4c4b4f;
    --photo-b: #2a292b;
  }
  * { margin: 0; padding: 0; box-sizing: border-box; }
  html, body { width: 734px; height: 1200px; overflow: hidden; background: var(--frame); }
  .card {
    position: relative;
    width: 734px;
    height: 1200px;
    border: 2px solid var(--frame);
    background: radial-gradient(ellipse at 50% 30%, var(--bg-top) 0%, var(--bg-bottom) 75%);
    overflow: hidden;
    font-family: "Montserrat", sans-serif;
    color: var(--white);
  }
  .ring { position: absolute; inset: 0; }
  .brand-mark {
    position: absolute;
    left: 222px;
    top: 98px;
    width: 66px;
    height: 66px;
    background: var(--orange);
  }
  .brand-name {
    position: absolute;
    left: 316px;
    top: 90px;
    font-weight: 800;
    color: var(--white);
    line-height: 1;
  }
  .brand-name .line-1 { display: block; font-size: 64px; letter-spacing: 1px; }
  .brand-name .line-2 { display: block; font-size: 25px; margin-top: 4px; letter-spacing: 0.5px; }
  .tagline {
    position: absolute;
    left: 262px;
    top: 190px;
    width: 300px;
    text-align: right;
    font-family: "Quicksand", sans-serif;
    font-size: 13px;
    color: var(--muted);
  }
  .portrait {
    position: absolute;
    left: 208px;
    top: 245px;
    width: 376px;
    height: 420px;
    border-radius: 150px 150px 0 0;
    background: linear-gradient(180deg, var(--photo-a) 0%, var(--photo-b) 70%, rgba(42,41,43,0) 100%);
  }
  .first-name {
    position: absolute;
    top: 622px;
    left: 0;
    width: 100%;
    text-align: center;
    font-weight: 900;
    font-style: italic;
    font-size: 172px;
    line-height: 1;
    letter-spacing: -2px;
  }
  .last-name {
    position: absolute;
    top: 780px;
    left: 0;
    width: 100%;
    text-align: center;
    font-weight: 700;
    font-size: 74px;
    line-height: 1;
    color: var(--orange);
  }
  .contacts {
    position: absolute;
    left: 106px;
    top: 890px;
    list-style: none;
    font-family: "Quicksand", sans-serif;
    font-weight: 400;
    font-size: 25px;
    color: var(--white);
  }
  .contacts li { display: flex; align-items: center; height: 35px; }
  .contacts li.spaced { margin-top: 4px; }
  .contacts svg { width: 20px; height: 20px; margin-right: 10px; flex: none; }
  .dot { width: 18px; height: 18px; border-radius: 50%; background: var(--white); margin: 0 11px 0 1px; flex: none; }
</style>
</head>
<body>
<div class="card">
  <svg class="ring" width="734" height="1200" viewBox="0 0 734 1200" aria-hidden="true">
    <defs>
      <linearGradient id="ringFade" x1="0" y1="420" x2="0" y2="830" gradientUnits="userSpaceOnUse">
        <stop offset="0" stop-color="#e49b2c"/>
        <stop offset="0.75" stop-color="#e49b2c" stop-opacity="0.5"/>
        <stop offset="1" stop-color="#e49b2c" stop-opacity="0"/>
      </linearGradient>
    </defs>
    <circle cx="367" cy="768" r="326" fill="none" stroke="url(#ringFade)" stroke-width="34"/>
    <circle cx="367" cy="768" r="282" fill="none" stroke="url(#ringFade)" stroke-width="6" opacity="0.25"/>
  </svg>

  <header class="brand">
    <span class="brand-mark"></span>
    <div class="brand-name"><span class="line-1">NOVA</span><span class="line-2">EVENTSERVICE</span></div>
    <p class="tagline">..für Feste, die in Erinnerung bleiben!</p>
  </header>

  <div class="portrait" role="img" aria-label="Porträtfoto des Inhabers in Weste und weißem Hemd mit verschränkten Armen"></div>

  <h1 class="first-name">JENS</h1>
  <h2 class="last-name">Wiesenthal</h2>

  <ul class="contacts">
    <li><svg viewBox="0 0 24 24"><path fill="#fff" d="M6.6 10.8a15.1 15.1 0 0 0 6.6 6.6l2.2-2.2c.3-.3.7-.4 1-.2 1.1.4 2.3.6 3.6.6.6 0 1 .4 1 1V20c0 .6-.4 1-1 1A17 17 0 0 1 3 4c0-.6.4-1 1-1h3.5c.6 0 1 .4 1 1 0 1.3.2 2.5.6 3.6.1.3 0 .7-.2 1z"/></svg>02345 678 12 34</li>
    <li><svg viewBox="0 0 24 24"><path fill="#fff" d="M6.6 10.8a15.1 15.1 0 0 0 6.6 6.6l2.2-2.2c.3-.3.7-.4 1-.2 1.1.4 2.3.6 3.6.6.6 0 1 .4 1 1V20c0 .6-.4 1-1 1A17 17 0 0 1 3 4c0-.6.4-1 1-1h3.5c.6 0 1 .4 1 1 0 1.3.2 2.5.6 3.6.1.3 0 .7-.2 1z"/></svg>0170 555 01 23</li>
    <li><svg viewBox="0 0 24 24" fill="none" stroke="#fff" stroke-width="1.4"><circle cx="12" cy="12" r="9"/><ellipse cx="12" cy="12" rx="4" ry="9"/><path d="M3 12h18M5 7h14M5 17h14"/></svg>www.nova-eventservice.de</li>
    <li><svg viewBox="0 0 24 24" fill="none" stroke="#fff" stroke-width="1.4"><rect x="3" y="6" width="18" height="12"/><path d="M3 6l9 7 9-7"/></svg>info@nova-eventservice.de</li>
    <li class="spaced"><svg viewBox="0 0 24 24" fill="none" stroke="#fff" stroke-width="1.5"><path d="M12 22s-6-7-6-12a6 6 0 0 1 12 0c0 5-6 12-6 12z"/><circle cx="12" cy="10" r="2"/></svg>Lindenweg 12, 45000 Musterstadt</li>
    <li><span class="dot"></span>www.socialpage.de/novaeventservice</li>
  </ul>
</div>
</body>
</html>
```